Business Card Design for Training Business

Clear Path Coaching is a new business that delivers training and other services with a focus on topics related to mental health and wellbeing, for example, Wellmind Response Course, Resilience etc. We have a strong focus on evidence-based psychology and neuroscience. I have a logo which I will upload with the brief, so please consider colours that work well with the logo.
Target Market(s)
Adults, workplaces (particularly government and not-for-profits)
Industry/Entity Type
Business
Contact Information for Business Card
Head Strong TrainingSamantha SellwoodDirector0438 770 bec@clearpathcoaching.example.au.auwww.headstrongtraining.com.au

```html
<!DOCTYPE html>
<html lang="en">
<head>
<meta charset="utf-8">
<title>Clear Path Coaching – Business Card</title>
<link rel="stylesheet" href="https://fonts.googleapis.com/css2?family=Roboto+Condensed:wght@300;400&display=swap">
<style>
  :root {
    --paper: #ffffff;
    --teal: #04b3bd;
    --teal-deep: #1d8d9c;
    --slate: #345a6c;
    --ink: #000000;
    --frame: #27a9e1;
    --text-dark: #111111;
    --text-light: #ffffff;
    --icon: #1fb5bf;
  }
  html, body {
    margin: 0;
    padding: 0;
    width: 1200px;
    height: 740px;
    overflow: hidden;
    background: var(--paper);
  }
  .card {
    position: relative;
    width: 1200px;
    height: 740px;
    font-family: "Roboto Condensed", sans-serif;
  }
  .card-art {
    position: absolute;
    inset: 0;
  }
  .brand-name {
    position: absolute;
    right: 445px;
    top: 208px;
    margin: 0;
    text-align: right;
    color: var(--text-light);
    font-weight: 300;
    text-transform: uppercase;
    line-height: 1;
  }
  .brand-name .line-main {
    display: block;
    font-size: 62px;
    letter-spacing: 5px;
  }
  .brand-name .line-sub {
    display: block;
    margin-top: 14px;
    font-size: 30px;
    letter-spacing: 13px;
    margin-right: -13px;
  }
  .person {
    position: absolute;
    left: 945px;
    top: 456px;
    transform: translateX(-50%);
    text-align: center;
    color: var(--text-light);
    white-space: nowrap;
  }
  .person-name {
    margin: 0;
    font-size: 31px;
    font-weight: 400;
    letter-spacing: 2.5px;
    text-transform: uppercase;
  }
  .person-role {
    margin: 2px 0 0;
    font-size: 21px;
    letter-spacing: 2.5px;
  }
  .contact-list {
    position: absolute;
    left: 70px;
    top: 476px;
    margin: 0;
    padding: 0;
    list-style: none;
  }
  .contact-item {
    display: flex;
    align-items: center;
    height: 53px;
    color: var(--text-dark);
    font-size: 31px;
    white-space: nowrap;
  }
  .contact-icon {
    width: 36px;
    height: 36px;
    margin-right: 16px;
    flex: none;
  }
</style>
</head>
<body>
<div class="card">
  <svg class="card-art" width="1200" height="740" viewBox="0 0 1200 740" aria-hidden="true">
    <defs>
      <linearGradient id="sweep-gradient" x1="0" y1="0" x2="1" y2="1">
        <stop offset="0" stop-color="var(--teal)"/>
        <stop offset="0.45" stop-color="var(--teal)"/>
        <stop offset="0.75" stop-color="var(--teal-deep)"/>
        <stop offset="1" stop-color="var(--slate)"/>
      </linearGradient>
      <filter id="sweep-shadow" x="-10%" y="-10%" width="130%" height="140%">
        <feDropShadow dx="-4" dy="22" stdDeviation="16" flood-color="#000" flood-opacity="0.45"/>
      </filter>
    </defs>
    <path class="sweep-band" filter="url(#sweep-shadow)"
          d="M18,95 Q470,560 1030,722 L1200,722 L1200,18 L415,18 Z"
          fill="url(#sweep-gradient)"/>
    <path class="dark-panel"
          d="M415,18 Q540,360 740,505 Q930,600 1200,568 L1200,18 Z"
          fill="var(--ink)"/>
    <rect class="inner-frame" x="44.5" y="44.5" width="1112" height="651"
          fill="none" stroke="var(--frame)" stroke-width="2"/>
    <circle class="brand-dot" cx="947" cy="256" r="160"
            fill="none" stroke="var(--teal)" stroke-width="4"/>
  </svg>

  <h1 class="brand-name">
    <span class="line-main">Clear Path</span>
    <span class="line-sub">Coaching</span>
  </h1>

  <div class="person">
    <p class="person-name">Rebecca Tanfield</p>
    <p class="person-role">Director</p>
  </div>

  <ul class="contact-list">
    <li class="contact-item">
      <svg class="contact-icon" viewBox="0 0 36 36" aria-hidden="true">
        <circle cx="18" cy="18" r="18" fill="var(--icon)"/>
        <path d="M12.5,9.5 l3,-0.5 l2,5 l-2,1.5 q1.5,3.5 5,5 l1.5,-2 l5,2 l-0.5,3 q-1,2 -3.5,1.5 q-11,-3 -12.5,-12.5 q0,-2.5 2,-3z" fill="#fff"/>
      </svg>
      +353 1 555 0192
    </li>
    <li class="contact-item">
      <svg class="contact-icon" viewBox="0 0 36 36" aria-hidden="true">
        <circle cx="18" cy="18" r="18" fill="var(--icon)"/>
        <g fill="none" stroke="#fff" stroke-width="1.6">
          <circle cx="18" cy="18" r="9"/>
          <ellipse cx="18" cy="18" rx="4" ry="9"/>
          <line x1="9" y1="18" x2="27" y2="18"/>
          <line x1="18" y1="9" x2="18" y2="27"/>
          <path d="M10.5,13.5 h15 M10.5,22.5 h15"/>
        </g>
      </svg>
      www.clearpathcoaching.example.au
    </li>
    <li class="contact-item">
      <svg class="contact-icon" viewBox="0 0 36 36" aria-hidden="true">
        <circle cx="18" cy="18" r="18" fill="var(--icon)"/>
        <rect x="9" y="12" width="18" height="12" fill="none" stroke="#fff" stroke-width="1.8"/>
        <path d="M9,12 L18,19.5 L27,12 M9,24 L15.5,17.5 M27,24 L20.5,17.5" fill="none" stroke="#fff" stroke-width="1.6"/>
      </svg>
      bec@clearpathcoaching.example.au
    </li>
    <li class="contact-item">
      <svg class="contact-icon" viewBox="0 0 36 36" aria-hidden="true">
        <circle cx="18" cy="18" r="18" fill="var(--icon)"/>
        <path d="M18,28 q-7,-8 -7,-12.5 a7,7 0 0 1 14,0 q0,4.5 -7,12.5z" fill="#fff"/>
        <circle cx="18" cy="15.5" r="2.8" fill="var(--icon)"/>
      </svg>
      42 Harbour Lane, Millbrook Road, Dublin, D04 K218
    </li>
  </ul>
</div>
</body>
</html>
```